Awesome photographers card for an awesome new business

Double sided business card Black background and silver logo in middle on one side. Details on otherside. please keep it simple

Industry/Entity Type

Photographer

Contact Information for Business Card

Gerald Fenwick
0452817360
GeraldFenwickPhotography47@mailbox.test
www.GeraldFenwickPhotography.test.au
Instagram _Gerald_fenwick

Requirements
Must have
• My logo in Silver
• please use instagram logo instead of "Instagram"

```html
<!DOCTYPE html>
<html lang="en">
<head>
<meta charset="utf-8">
<title>Gerald Fenwick Photography – Business Card</title>
<link rel="stylesheet" href="https://fonts.googleapis.com/css2?family=Open+Sans:wght@400;600;700&display=swap">
<style>
  :root {
    --page-bg: #e4e5e7;
    --card-light-top: #eef0f1;
    --card-light-bottom: #d3d6d9;
    --card-dark: #3d3e41;
    --card-dark-edge: #5a5c60;
    --silver: #c9ccd0;
    --name-ink: #2a2b2d;
    --brand-ink: #4a4c50;
    --contact-ink: #d8dadd;
  }
  * { margin: 0; padding: 0; box-sizing: border-box; }
  html, body {
    width: 1200px;
    height: 969px;
    overflow: hidden;
    background: var(--page-bg);
    font-family: "Open Sans", Arial, sans-serif;
  }
  .business-card {
    position: absolute;
    left: 120px;
    top: 212px;
    width: 960px;
    height: 545px;
    border-radius: 28px;
    overflow: hidden;
    box-shadow: 0 10px 30px rgba(0,0,0,0.15);
  }
  .card-surface { position: absolute; inset: 0; display: block; }
  .brand-mark {
    position: absolute;
    left: 120px;
    top: 98px;
    display: flex;
    align-items: center;
    gap: 14px;
  }
  .brand-dot {
    width: 18px;
    height: 18px;
    border-radius: 50%;
    background: var(--brand-ink);
  }
  .brand-name {
    font-weight: 600;
    font-size: 26px;
    color: var(--brand-ink);
    letter-spacing: 0.5px;
  }
  .holder-name {
    position: absolute;
    right: 62px;
    top: 70px;
    font-weight: 700;
    font-size: 28px;
    letter-spacing: 0.6px;
    color: var(--name-ink);
    text-transform: uppercase;
  }
  .contact-list {
    position: absolute;
    left: 64px;
    top: 382px;
    list-style: none;
  }
  .contact-item {
    display: flex;
    align-items: center;
    height: 31px;
    font-size: 21px;
    color: var(--contact-ink);
  }
  .contact-icon {
    width: 20px;
    height: 20px;
    margin-right: 22px;
    flex: none;
    fill: var(--contact-ink);
  }
  .handle-square {
    width: 18px;
    height: 18px;
    margin: 0 24px 0 1px;
    background: var(--contact-ink);
    flex: none;
  }
</style>
</head>
<body>
  <div class="business-card">
    <svg class="card-surface" viewBox="0 0 960 545" width="960" height="545">
      <defs>
        <linearGradient id="lightFace" x1="0" y1="0" x2="0" y2="1">
          <stop offset="0" stop-color="var(--card-light-top)"/>
          <stop offset="1" stop-color="var(--card-light-bottom)"/>
        </linearGradient>
        <linearGradient id="darkFace" x1="0" y1="0" x2="1" y2="1">
          <stop offset="0" stop-color="var(--card-dark-edge)"/>
          <stop offset="0.5" stop-color="var(--card-dark)"/>
          <stop offset="1" stop-color="#2f3033"/>
        </linearGradient>
      </defs>
      <rect class="light-face" width="960" height="545" fill="url(#lightFace)"/>
      <path class="dark-sweep" d="M0,0 H60 C30,150 110,250 260,290 C520,350 860,380 960,530 V545 H0 Z" fill="url(#darkFace)"/>
      <path class="silver-swoosh" d="M74,0 C44,150 124,238 272,276 C532,336 872,364 960,505" fill="none" stroke="var(--silver)" stroke-width="6"/>
    </svg>

    <div class="brand-mark">
      <span class="brand-dot"></span>
      <span class="brand-name">Fenwick Photography</span>
    </div>

    <div class="holder-name">Gerald Fenwick</div>

    <ul class="contact-list">
      <li class="contact-item">
        <svg class="contact-icon" viewBox="0 0 24 24"><path d="M6.6 10.8a15.1 15.1 0 0 0 6.6 6.6l2.2-2.2a1 1 0 0 1 1-.25 11.4 11.4 0 0 0 3.6.57 1 1 0 0 1 1 1V20a1 1 0 0 1-1 1A17 17 0 0 1 3 4a1 1 0 0 1 1-1h3.5a1 1 0 0 1 1 1c0 1.25.2 2.45.57 3.57a1 1 0 0 1-.25 1z"/></svg>
        <span>0452817360</span>
      </li>
      <li class="contact-item">
        <svg class="contact-icon" viewBox="0 0 24 24"><path d="M2 5h20v14H2z M4 7v.3l8 5 8-5V7l-8 5z" fill-rule="evenodd"/></svg>
        <span>GeraldFenwickPhotography47@mailbox.test</span>
      </li>
      <li class="contact-item">
        <svg class="contact-icon" viewBox="0 0 24 24"><path d="M12 2a10 10 0 1 0 0 20 10 10 0 0 0 0-20zm0 2c1 0 2.3 2 2.8 5H9.2C9.7 6 11 4 12 4zM4.3 11h3.8a17 17 0 0 0 0 2H4.3a8 8 0 0 1 0-2zm5.7 0h4a15 15 0 0 1 0 2h-4a15 15 0 0 1 0-2zm5.9 0h3.8a8 8 0 0 1 0 2h-3.8a17 17 0 0 0 0-2zM9.2 15h5.6c-.5 3-1.8 5-2.8 5s-2.3-2-2.8-5z"/></svg>
        <span>www.GeraldFenwickPhotography.test.au</span>
      </li>
      <li class="contact-item">
        <span class="handle-square"></span>
        <span>_Gerald_fenwick</span>
      </li>
    </ul>
  </div>
</body>
</html>
```